Calm Harbor Bodywork business is seeking a Business Card Design

We are a new natural therapy business that needs a Business Card Design with an appointment card on the back.

We offer Myotherapy (muscle therapy) services and have a strong focus and commitment to helping people relieve pain and restore movement to their bodies.

I am attaching my business logo for you information.

Business card must contain my logo and have space for name, title, qualifications, phone number, email, web address

Appointment Card on the back of the card must contain space to write next appointment date, time and name of therapist and cancellation policy.

Cancellation Policy
Minimum of 24hrs notice is required prior to appointment time or full treatment fees with apply.

```html
<!DOCTYPE html>
<html lang="en">
<head>
<meta charset="utf-8">
<title>Tideline Myotherapy – Business and Appointment Card</title>
<link href="https://fonts.googleapis.com/css2?family=Open+Sans:wght@400;600;700&display=swap" rel="stylesheet">
<style>
  :root {
    --brand-red: #c01f31;
    --brand-green: #7dbf3b;
    --ink-dark: #3a3a3a;
    --paper: #ffffff;
    --backdrop: #e9e6e1;
    --line-soft: rgba(255,255,255,0.75);
  }
  html, body {
    margin: 0;
    width: 1200px;
    height: 865px;
    overflow: hidden;
    background: var(--backdrop);
    font-family: "Open Sans", sans-serif;
  }
  .card {
    position: absolute;
    top: 270px;
    width: 570px;
    height: 326px;
    box-shadow: 0 8px 24px rgba(0,0,0,0.18);
    overflow: hidden;
  }
  .card.front { left: 20px; background: var(--paper); }
  .card.back  { left: 610px; background: var(--brand-red); color: var(--paper); }

  /* front */
  .card-top { position: absolute; left: 0; top: 0; width: 100%; height: 182px; }
  .accent-line {
    position: absolute; left: 0; top: 182px;
    width: 100%; height: 7px; background: var(--brand-green);
  }
  .card-bottom {
    position: absolute; left: 0; top: 189px;
    width: 100%; height: 137px;
    background: var(--brand-red); color: var(--paper);
  }
  .brand { position: absolute; left: 36px; top: 40px; }
  .brand-row { display: flex; align-items: center; gap: 10px; }
  .brand-square { width: 34px; height: 34px; background: var(--brand-red); }
  .brand-name {
    font-size: 22px; font-weight: 700;
    color: var(--brand-red); letter-spacing: 0.3px; white-space: nowrap;
  }
  .brand-tagline {
    margin: 4px 0 0 44px; font-size: 10px;
    color: var(--brand-green); letter-spacing: 0.4px;
  }
  .person { position: absolute; right: 32px; top: 34px; text-align: right; }
  .person-name {
    font-size: 20px; font-weight: 700;
    color: var(--ink-dark); letter-spacing: 0.6px; line-height: 1.2;
  }
  .person-title { font-size: 12px; color: var(--ink-dark); margin-top: 1px; }
  .person-qualifications { font-size: 10px; color: var(--ink-dark); margin-top: 2px; opacity: 0.85; }
  .address {
    position: absolute; left: 36px; top: 122px;
    display: flex; align-items: center; gap: 10px;
    font-size: 12px; line-height: 1.35; color: var(--ink-dark);
  }
  .contact-list { position: absolute; top: 32px; list-style: none; margin: 0; padding: 0; }
  .contact-list.left { left: 36px; }
  .contact-list.right { left: 312px; }
  .contact-item {
    display: flex; align-items: center; gap: 9px;
    font-size: 13px; font-weight: 600; height: 36px; white-space: nowrap;
  }
  .icon-slot { width: 15px; display: flex; justify-content: center; flex: none; }

  /* back */
  .back-stripe {
    position: absolute; left: 22px; top: 0;
    width: 9px; height: 100%; background: var(--brand-green);
  }
  .appointment { position: absolute; left: 58px; top: 30px; right: 34px; }
  .appointment-title {
    font-size: 18px; font-weight: 700; letter-spacing: 0.6px;
    margin: 0 0 18px;
  }
  .field { display: flex; align-items: flex-end; gap: 8px; font-size: 12px; font-weight: 600; height: 34px; }
  .field-line { flex: 1; border-bottom: 1px solid var(--line-soft); margin-bottom: 3px; }
  .field-row { display: flex; gap: 22px; }
  .field-row .field { flex: 1; }
  .policy { margin-top: 22px; font-size: 10.5px; line-height: 1.45; }
  .policy-title { font-weight: 700; font-size: 11px; letter-spacing: 0.4px; margin-bottom: 2px; }
</style>
</head>
<body>
  <div class="card front">
    <section class="card-top">
      <div class="brand">
        <div class="brand-row">
          <div class="brand-square"></div>
          <div class="brand-name">Tideline Myotherapy</div>
        </div>
        <div class="brand-tagline">Calm Harbor Bodywork</div>
      </div>

      <div class="person">
        <div class="person-name">MARCUS HALE</div>
        <div class="person-title">Managing Director</div>
        <div class="person-qualifications">B.Hlth Sci (Myotherapy)</div>
      </div>

      <div class="address">
        <svg width="13" height="18" viewBox="0 0 22 30" aria-hidden="true">
          <path d="M11 0C4.9 0 0 4.9 0 11c0 8 11 19 11 19s11-11 11-19C22 4.9 17.1 0 11 0z" fill="#3a3a3a"/>
          <circle cx="11" cy="11" r="4.2" fill="#fff"/>
        </svg>
        <div>41 Quayside Lane, Level 2<br>Harbour Road</div>
      </div>
    </section>

    <div class="accent-line"></div>

    <section class="card-bottom">
      <ul class="contact-list left">
        <li class="contact-item">
          <span class="icon-slot"><svg width="11" height="16" viewBox="0 0 20 28" aria-hidden="true">
            <rect x="1.5" y="1.5" width="17" height="25" rx="2.5" fill="none" stroke="#fff" stroke-width="2.5"/>
            <circle cx="10" cy="22" r="1.6" fill="#fff"/>
          </svg></span>
          013 482 5570
        </li>
        <li class="contact-item">
          <span class="icon-slot"><svg width="14" height="14" viewBox="0 0 24 24" aria-hidden="true">
            <circle cx="12" cy="12" r="10.5" fill="none" stroke="#fff" stroke-width="2"/>
            <ellipse cx="12" cy="12" rx="4.5" ry="10.5" fill="none" stroke="#fff" stroke-width="1.6"/>
            <line x1="1.5" y1="12" x2="22.5" y2="12" stroke="#fff" stroke-width="1.6"/>
          </svg></span>
          www.calmharbor.com
        </li>
      </ul>
      <ul class="contact-list right">
        <li class="contact-item">
          <span class="icon-slot"><svg width="13" height="13" viewBox="0 0 24 24" aria-hidden="true">
            <path d="M6.6 10.8a15 15 0 0 0 6.6 6.6l2.2-2.2c.3-.3.7-.4 1-.2 1.1.4 2.3.6 3.6.6.6 0 1 .4 1 1V20c0 .6-.4 1-1 1C10.6 21 3 13.4 3 4c0-.6.4-1 1-1h3.5c.6 0 1 .4 1 1 0 1.3.2 2.5.6 3.6.1.3 0 .7-.2 1z" fill="#fff"/>
          </svg></span>
          013 482 5570
        </li>
        <li class="contact-item">
          <span class="icon-slot"><svg width="14" height="11" viewBox="0 0 24 18" aria-hidden="true">
            <rect x="0" y="0" width="24" height="18" rx="2" fill="#fff"/>
            <path d="M1 1.5l11 8.5 11-8.5" fill="none" stroke="#c01f31" stroke-width="1.8"/>
          </svg></span>
          book@calmharbor.com
        </li>
      </ul>
    </section>
  </div>

  <div class="card back">
    <div class="back-stripe"></div>
    <section class="appointment">
      <h2 class="appointment-title">YOUR NEXT APPOINTMENT</h2>
      <div class="field">Therapist <span class="field-line"></span></div>
      <div class="field-row">
        <div class="field">Date <span class="field-line"></span></div>
        <div class="field">Time <span class="field-line"></span></div>
      </div>
      <div class="policy">
        <div class="policy-title">Cancellation Policy</div>
        Minimum of 24hrs notice is required prior to appointment time or full treatment fees will apply.
      </div>
    </section>
  </div>
</body>
</html>
```